Letterhead Design for Law Firm

**Edit: I have added the photo of a bottom that I like.

------
We are looking for a re-design of our new letterhead. The letterhead is for a law firm and will be used for digital and traditionally printed correspondence.

Here are some suggestions:

- Please use colours are #8ec900 and simple black.
- Please do not use any type of "waves" at the bottom of the page. This is not in style at all.
- Please stay modern yet conservative.
- Please use font Segoe UI Light or similar if you can
- Avoid clipart or illustrations.
- Utilize ample white space in the layout so the design looks clean and information is easy to read at a glance. Don't overcrowd the letterhead.
- Make sure the letterhead design is consistent with our brand identity (see corvelith.ca)
-Please, no black headers or footers.

I am attaching my current letterhead and signature for your convenience.

Remember, the letterhead is an extension of our professional identity. We are a successful firm and trial lawyers who correspond with insurers, judges, lawyers, courts, clients, etc. Make it new, modern, attractive, yet powerful and conservative.

It needs to be easily printable. I would like the bleed removed in print so the black bar the bottom crosses the page (but the text is not near the edges)
Updates

Low design quality

Target Market(s)

Clients, Government Offices, Judiciary, Lawyers, Insurance Companies, Colleagues.

Industry/Entity Type

Law

Other font styles liked:
• Segoe UI LIght, Calibri Light,

Colors
00AB8E
00BBA5
67D7C9
C6EFE9
E9F9F6

Requirements
Must have
• Everything that is on the letterhead now.
Nice to have
• Cutting Edge design, yet conservative.
Should not have
• law firm cliche design, images,

```html
<!DOCTYPE html>
<html lang="en">
<head>
<meta charset="utf-8">
<title>Varenne Personal Injury Lawyers – Letterhead</title>
<link href="https://fonts.googleapis.com/css2?family=Open+Sans:wght@300;400;600;700&display=swap" rel="stylesheet">
<style>
  :root {
    --brand-green: #8ec900;
    --ink: #111111;
    --text: #222222;
    --paper: #ffffff;
    --backdrop: #d9d9d9;
  }
  * { box-sizing: border-box; margin: 0; padding: 0; }
  html, body { width: 1200px; height: 1155px; overflow: hidden; }
  body {
    background: var(--backdrop);
    font-family: "Open Sans", "Segoe UI", Calibri, sans-serif;
    color: var(--text);
    position: relative;
  }
  .sheet {
    position: absolute;
    left: 170px; top: 21px;
    width: 860px; height: 1113px;
    background: var(--paper);
    overflow: hidden;
    box-shadow: 0 4px 18px rgba(0,0,0,0.18);
  }
  .firm-name {
    position: absolute; left: 60px; top: 92px;
    font-size: 64px; font-weight: 400; letter-spacing: 1px;
    color: var(--ink); line-height: 1;
  }
  .firm-tagline {
    position: absolute; left: 64px; top: 168px;
    font-size: 15px; font-weight: 400; letter-spacing: 3px;
    color: var(--ink);
  }
  .contact-block {
    position: absolute; left: 548px; top: 62px;
    border-left: 3px solid var(--brand-green);
    padding-left: 12px;
    font-size: 12.5px; line-height: 1.42; color: var(--text);
    font-style: normal;
  }
  .contact-block .web-accent { color: var(--brand-green); font-weight: 600; }
  .contact-block b { font-weight: 700; }
  .contact-block .practice { margin-top: 14px; }
  .contact-block .practice-title { font-weight: 700; }

  .letter { position: absolute; left: 80px; top: 252px; font-size: 14px; line-height: 1.45; }
  .letter .label { font-weight: 600; }
  .letter p { margin-bottom: 16px; }
  .recipient { margin-bottom: 22px; }
  .subject {
    position: absolute; left: 80px; top: 560px; width: 720px;
    border-top: 1px solid var(--ink); border-bottom: 1px solid var(--ink);
    padding: 10px 0; display: flex; font-size: 14px; line-height: 1.45;
  }
  .subject .re { width: 180px; font-weight: 600; }
  .subject .lines { font-weight: 600; }
  .subject sup { font-size: 9px; }

  .sign-off { position: absolute; left: 80px; top: 810px; font-size: 14px; line-height: 1.45; }
  .sign-off .firm-caps { font-weight: 600; }
  .signature-mark {
    width: 220px; height: 48px; margin: 8px 0 6px;
    background: linear-gradient(90deg, #e8e8e8, #f4f4f4);
  }
  .sign-off .corp { font-weight: 600; font-size: 13px; }
  .sign-off .small { font-size: 13px; }

  .footer-rule {
    position: absolute; left: 0; bottom: 34px;
    width: 860px; height: 3px; background: var(--ink);
  }
  .footer-band {
    position: absolute; left: 0; bottom: 0;
    width: 860px; height: 26px; background: var(--brand-green);
  }
</style>
</head>
<body>
  <main class="sheet">
    <div class="firm-name">VARENNE</div>
    <div class="firm-tagline">PERSONAL INJURY LAWYERS</div>

    <address class="contact-block">
      <div>www.<span class="web-accent">CORVELITH</span>.ca</div>
      <div>48 Alder Street W., Suite 1210</div>
      <div>Brantford, ON&nbsp; N3T 2K7</div>
      <div><b>T:</b> 905-555-0142</div>
      <div><b>F:</b> 905-555-0187</div>
      <div><b>File Clerk:</b> Maren Holloway</div>
      <div><b>Email:</b> maren@corvelith.ca</div>
      <div class="practice">
        <div class="practice-title">Practice Restricted</div>
        <div>Serious Personal Injury</div>
        <div>Wrongful Death Litigation</div>
        <div>Long-Term Disability Litigation</div>
        <div>Wrongful Dismissal Litigation</div>
        <div>Employee Terminations</div>
      </div>
    </address>

    <section class="letter">
      <p class="label">Without Prejudice</p>
      <p>March 13, 2024</p>
      <p class="label">By Email</p>
      <div class="recipient">
        Northmere Insurance Company<br>
        Claims Litigation Department<br>
        240 Kingsway Road South<br>
        P.O. Box 3100<br>
        Waterloo, ON&nbsp;&nbsp; N2J 5R2
      </div>
      <p>Attention:&nbsp; Mr. Devin Marsh</p>
      <p>Mr. Marsh:</p>
    </section>

    <section class="subject">
      <div class="re">Re:</div>
      <div class="lines">
        Pellham v. Ostrova et al.<br>
        DOL:&nbsp; September 12, 2019<br>
        Pre-Mediation Settlement Proposal – March 13<sup>th</sup>, 2024
      </div>
    </section>

    <section class="sign-off">
      <div>Yours very truly,</div>
      <div class="firm-caps">VARENNE PERSONAL INJURY LAWYERS</div>
      <div class="signature-mark" role="img" aria-label="Handwritten signature of Owen T. Varenne"></div>
      <div>Owen T. Varenne</div>
      <div class="corp">Varenne Law Professional Corporation</div>
      <div class="small">/mh</div>
      <div class="small">Encl.</div>
    </section>

    <div class="footer-rule" aria-hidden="true"></div>
    <div class="footer-band" aria-hidden="true"></div>
  </main>
</body>
</html>
```